Volunteer fire fighters needed banner

As part of our recruitment campaign, we need a sign we can post on our sign trailer to entice locals to join our volunteer fire service. This design will be printed on a banner, front and back, to catch traffic going in both directions on a busy roadway. This banner will have a printed surface of 4 feet tall by 8 feet long.
Our fire department is looking to attract people between the ages of 18 and 35 years old who are interested in being a firefighter. We offer our volunteers:
-Free professional training
-All equipment supplied
-Tax abatements for active volunteers
For more information, you can check us out at:
Brackenmoorfire.example

This design should:
-scale to and fit a 4'x8' canvas
-Include our web address "BrackenMoorFire.example"
-Say "Members Wanted"
-"Drill every Tuesday at 7pm"
-"57 Kestrel Pond Lane"
-Include "Bracken Moor Fire Department"

We've included reference photos and past images we use for our other campaigns for inspiration for you.

Target Market(s)

18-35 y/o

Industry/Entity Type

Fire Service

Requirements
Must have
• -scale to and fit a 4'x8' canvas -Include our web address "BrackenMoorFire.example" -Say "Members Wanted" -"Drill every Tuesday at 7pm" -"57 Kestrel Pond Lane" -Include "Bracken Moor Fire Department"

```html
<!DOCTYPE html>
<html lang="en">
<head>
<meta charset="utf-8">
<title>Members Wanted – Bracken Moor Fire Department</title>
<link href="https://fonts.googleapis.com/css2?family=Montserrat:ital,wght@0,500;0,600;0,700;0,800;0,900;1,900&display=swap" rel="stylesheet">
<style>
  :root{
    --stage:#2e2e2e;
    --navy:#363b78;
    --paper:#efedee;
    --panel:#cfcdcf;
    --ink:#2f2a2b;
    --red:#dc1420;
    --orange:#f6861f;
    --yellow:#fbb61b;
    --white:#ffffff;
  }
  *{margin:0;padding:0;box-sizing:border-box}
  html,body{width:1200px;height:1200px;overflow:hidden;background:var(--stage)}
  body{font-family:"Montserrat",Arial,sans-serif;position:relative}
  .banner{position:absolute;left:0;top:300px;width:1200px;height:600px;background:var(--paper);overflow:hidden}
  .banner-shapes{position:absolute;inset:0}

  .dept-name{position:absolute;left:34px;top:40px;width:140px;height:130px;color:var(--white);font-weight:700;font-size:16px;line-height:1.2;text-align:center;display:flex;flex-direction:column;align-items:center;justify-content:center;gap:10px}
  .dept-name .dot{width:16px;height:16px;border-radius:50%;background:var(--white)}

  .headline{position:absolute;left:183px;top:40px;font-weight:900;font-style:italic;font-size:78px;line-height:.84;letter-spacing:-2px;color:var(--red);-webkit-text-stroke:7px var(--white);paint-order:stroke fill;text-shadow:0 6px 10px rgba(0,0,0,.35);text-transform:uppercase;transform:scaleY(1.12);transform-origin:left top}
  .headline span{display:block}
  .headline .second{margin-left:18px}

  .intro{position:absolute;left:44px;top:216px;width:576px;text-align:center;color:var(--ink);font-weight:600;font-size:21.5px;line-height:1.2}

  .offer-panel{position:absolute;left:48px;top:329px;width:585px;height:129px;background:var(--panel);border-radius:12px}
  .offer-title{position:absolute;left:127px;top:305px;width:407px;height:48px;border-radius:16px;background:linear-gradient(90deg,var(--orange),var(--red));color:var(--white);font-weight:800;font-size:21px;display:flex;align-items:center;justify-content:center;-webkit-text-stroke:3px #5a2a10;paint-order:stroke fill}
  .offer-list{position:absolute;left:70px;top:359px;list-style:none}
  .offer-list li{display:flex;align-items:center;gap:9px;height:29px;font-weight:700;font-size:21.5px;color:var(--ink);white-space:nowrap}
  .offer-list svg{width:19px;height:22px;flex:none}

  .info-bar{position:absolute;left:0;top:471px;width:703px;height:51px;background:var(--yellow);border-radius:0 8px 8px 0;display:flex;align-items:center;justify-content:center;font-weight:600;font-size:24.5px;color:var(--ink);padding-left:20px;white-space:nowrap}

  .contact{position:absolute;left:0;top:522px;width:860px;height:77px;display:flex;align-items:center;color:var(--white);white-space:nowrap}
  .address{display:flex;align-items:center;gap:9px;margin-left:42px;font-weight:600;font-size:22px}
  .address svg{width:22px;height:32px;flex:none}
  .divider{width:3px;height:36px;background:var(--red);margin:0 22px 0 20px;flex:none}
  .web{font-weight:600;font-size:27px;letter-spacing:1px}

  .drill{position:absolute;left:603px;top:182px}
  .drill-text{position:absolute;left:605px;top:238px;width:200px;text-align:center;font-weight:800;font-size:27px;line-height:1.05;color:var(--red);-webkit-text-stroke:5px var(--white);paint-order:stroke fill;letter-spacing:-.5px;white-space:nowrap}

  .station-mark{position:absolute;left:1015px;top:30px;width:165px;height:110px;display:flex;align-items:center;justify-content:center;color:var(--white);font-weight:700;font-size:17px;line-height:1.2;text-align:center}
</style>
</head>
<body>
<section class="banner" aria-label="Members wanted recruitment banner">
  <svg class="banner-shapes" viewBox="0 0 1200 600" width="1200" height="600">
    <defs>
      <linearGradient id="truckTone" x1="0" y1="0" x2="1" y2="1">
        <stop offset="0" stop-color="#d9d4cf"/>
        <stop offset=".35" stop-color="#c2202a"/>
        <stop offset=".75" stop-color="#8e1218"/>
        <stop offset="1" stop-color="#3b3435"/>
      </linearGradient>
      <linearGradient id="ringTone" x1="0" y1="0" x2="0" y2="1">
        <stop offset="0" stop-color="#f7a01e"/>
        <stop offset="1" stop-color="#e2261f"/>
      </linearGradient>
      <linearGradient id="crewTone" x1="0" y1="0" x2="1" y2="1">
        <stop offset="0" stop-color="#5c544f"/>
        <stop offset=".5" stop-color="#8a6a4a"/>
        <stop offset="1" stop-color="#3a3330"/>
      </linearGradient>
      <linearGradient id="rescueTone" x1="0" y1="0" x2="1" y2="1">
        <stop offset="0" stop-color="#e6e3e4"/>
        <stop offset=".5" stop-color="#8a6a4a"/>
        <stop offset="1" stop-color="#b51c22"/>
      </linearGradient>
    </defs>
    <rect class="top-band" x="0" y="0" width="700" height="206" fill="var(--navy)"/>
    <path class="truck-photo" role="img" aria-label="Photo of a red fire engine parked in the station bay" d="M652,0 H1200 V498 H760 Q690 300 652 0 Z" fill="url(#truckTone)"/>
    <path class="swoosh" d="M621,0 H652 Q668 180 720 300 L700 310 Q640 170 621 0 Z" fill="var(--orange)"/>
    <rect class="bottom-band" x="0" y="498" width="1200" height="102" fill="var(--navy)"/>
    <circle cx="904" cy="420" r="131" fill="url(#ringTone)"/>
    <circle class="crew-photo" role="img" aria-label="Photo of firefighters in breathing gear working a hose line" cx="904" cy="420" r="121" fill="url(#crewTone)"/>
    <circle cx="1087" cy="479" r="97" fill="url(#ringTone)"/>
    <circle class="rescue-photo" role="img" aria-label="Photo of firefighters at a vehicle rescue in the snow" cx="1087" cy="479" r="88" fill="url(#rescueTone)"/>
  </svg>

  <div class="dept-name"><span class="dot"></span>Bracken Moor Fire Department</div>

  <h1 class="headline"><span>Members</span><span class="second">Wanted</span></h1>

  <div class="station-mark">Bracken Moor<br>Fire Department</div>

  <svg class="drill" width="200" height="200" viewBox="-4 -4 208 208" aria-hidden="true">
    <polygon points="198,100 179.2,121.2 184.9,149 158,158 149,184.9 121.2,179.2 100,198 78.8,179.2 51,184.9 42,158 15.1,149 20.8,121.2 2,100 20.8,78.8 15.1,51 42,42 51,15.1 78.8,20.8 100,2 121.2,20.8 149,15.1 158,42 184.9,51 179.2,78.8" fill="var(--navy)" stroke="var(--white)" stroke-width="4" stroke-linejoin="round"/>
  </svg>
  <p class="drill-text">Drill every<br>Tuesday<br>at 7pm</p>

  <p class="intro">Our fire department is looking to attract people between the ages of 18 and 35 years old who are interested in being a firefighter.</p>

  <div class="offer-panel"></div>
  <div class="offer-title">WE OFFER OUR VOLUNTEERS:</div>
  <ul class="offer-list">
    <li><svg viewBox="0 0 18 20"><path d="M1 11 L7 18 L17 1 L7 13 Z" fill="var(--red)"/></svg>FREE PROFESSIONAL TRAINING</li>
    <li><svg viewBox="0 0 18 20"><path d="M1 11 L7 18 L17 1 L7 13 Z" fill="var(--red)"/></svg>ALL EQUIPMENT SUPPLIED</li>
    <li><svg viewBox="0 0 18 20"><path d="M1 11 L7 18 L17 1 L7 13 Z" fill="var(--red)"/></svg>TAX ABATEMENTS FOR ACTIVE VOLUNTEERS</li>
  </ul>

  <div class="info-bar">For more information, you can check us out at:</div>

  <div class="contact">
    <div class="address">
      <svg viewBox="0 0 22 32" aria-hidden="true"><path d="M11 1 C5 1 2 5 2 10 C2 16 11 25 11 25 C11 25 20 16 20 10 C20 5 17 1 11 1 Z" fill="var(--red)"/><circle cx="11" cy="10" r="3.5" fill="var(--navy)"/><ellipse cx="11" cy="28" rx="7" ry="2.5" fill="none" stroke="#111" stroke-width="2"/></svg>
      57 Kestrel Pond Lane
    </div>
    <span class="divider"></span>
    <span class="web">www.BrackenMoorFire.example</span>
  </div>
</section>
</body>
</html>
```